Investment Management Firm Power point template

Marrow Holdings is a real estate investment firm focused on buying commercial office and residential property in the UK. We produce powerpoint presentations for our Board of Directors, Investment Committee and also to external investors.

We are looking for a powerpoint design template which we can use for future presentations which provide a professional look and feel.

Our current website: http://www.marrowholdings.example.co.uk/

Target Market(s)

Institution Investors, Board of Directors, Professionals

Industry/Entity Type

Real Estate

Requirements
Must have
• Leverage off the current logo and colour scheme. However, does not have to purely rely on this colour scheme.
• - Title page
• - Content Page
• - Slide where graphs can be incorporated
• - Slide where photos can be incorporated
• - Slide of UK Map which can show where the property portfolio is currently located
• - Other slides incorporating smart art or other designs that can be used for future presentations
Nice to have
• An example of graphics that we would love to have in the powerpoint pack which we can easily edit has been attached

```html
<!DOCTYPE html>
<html lang="en">
<head>
<meta charset="UTF-8">
<title>About Us</title>
<link rel="stylesheet" href="https://fonts.googleapis.com/css2?family=Cabin:wght@400;600;700&display=swap">
<style>
  :root {
    --page-bg: #f7f8f9;
    --heading-teal: #17587a;
    --rule: #1f3a4a;
    --caption-bar: #545556;
    --caption-text: #ffffff;
    --body-text: #3d3d3d;
    --footer-band: #343536;
    --photo-sky: #b9a98a;
    --photo-sun: #e8c98a;
    --photo-water: #5b5450;
  }
  * { margin: 0; padding: 0; box-sizing: border-box; }
  html, body { width: 1200px; height: 900px; overflow: hidden; }
  body { font-family: "Cabin", sans-serif; background: var(--page-bg); }

  .slide {
    position: relative;
    width: 1200px;
    height: 900px;
    overflow: hidden;
    background:
      radial-gradient(ellipse 620px 260px at 180px 40px, rgba(200,203,206,0.45), rgba(200,203,206,0) 70%),
      var(--page-bg);
  }

  .slide-title {
    position: absolute;
    top: 22px;
    left: 0;
    width: 1200px;
    text-align: center;
    font-size: 40px;
    font-weight: 700;
    color: var(--heading-teal);
  }
  .slide-title-rule {
    position: absolute;
    top: 76px;
    left: 470px;
    width: 262px;
    height: 2px;
    background: var(--rule);
  }

  .image-caption {
    position: absolute;
    top: 198px;
    left: 0;
    width: 640px;
    height: 60px;
    background: var(--caption-bar);
    color: var(--caption-text);
    font-size: 33px;
    font-weight: 600;
    text-align: right;
    padding-right: 18px;
    line-height: 60px;
  }

  .feature-photo {
    position: absolute;
    top: 264px;
    left: 0;
    width: 640px;
    height: 501px;
    background: linear-gradient(180deg,
      #8f8fa8 0%,
      var(--photo-sky) 30%,
      var(--photo-sun) 50%,
      #6e6153 60%,
      var(--photo-water) 100%);
  }

  .body-copy {
    position: absolute;
    top: 193px;
    left: 668px;
    width: 462px;
    font-size: 20.5px;
    line-height: 30px;
    color: var(--body-text);
  }
  .body-copy p + p { margin-top: 30px; }

  .footer-band {
    position: absolute;
    left: 0;
    bottom: 0;
    width: 1200px;
    height: 39px;
    background: var(--footer-band);
  }
</style>
</head>
<body>
  <main class="slide">
    <h1 class="slide-title">About Us</h1>
    <div class="slide-title-rule"></div>

    <div class="image-caption">Image Title Here</div>
    <div class="feature-photo" role="img" aria-label="Photograph of a city river at sunset with a bridge and a tall glass tower on the skyline"></div>

    <section class="body-copy">
      <p>Lorem ipsum dolor sit ipsum Lorem ipsum dolor sit ipsum Lorem ipsum dolor sit ipsum Lorem ipsum dolor sit ipsum Lorem ipsum dolor sit ipsum Lorem ipsum dolor sit ipsum</p>
      <p>Lorem ipsum dolor sit ipsum Lorem ipsum dolor sit ipsum Lorem ipsum dolor sit ipsum Lorem ipsum dolor sit ipsum Lorem ipsum dolor sit ipsum Lorem ipsum dolor sit ipsum Lorem ipsum dolor sit ipsum Lorem ipsum dolor sit ipsum Lorem ipsum dolor sit ipsum Lorem ipsum dolor sit ipsum</p>
      <p>Lorem ipsum dolor sit ipsum Lorem ipsum dolor sit ipsum Lorem ipsum dolor sit ipsum Lorem ipsum dolor sit ipsum</p>
      <p>Lorem ipsum dolor sit ipsum Lorem ipsum dolor sit ipsum Lorem ipsum dolor sit ipsum Lorem ipsum dolor sit ipsum</p>
    </section>

    <div class="footer-band"></div>
  </main>
</body>
</html>
```